Business Card Design (NEW FILES)

ATTENTION: New vector files are available. Please update your design to reflect/use the new (better resolution) logo images.

Seeking a unique and professional business card design for a commercial drone photography/videography business. The layout should feature
the logo (attached) and include the following information:
Owen Tarrick
614-502-7738
www.skylarkreelworks.example
NRD Certified Remote Pilot

Owen Tarrick

```html
<!DOCTYPE html>
<html lang="en">
<head>
<meta charset="utf-8">
<title>Skylark Reelworks Business Card</title>
<link href="https://fonts.googleapis.com/css2?family=Montserrat:wght@400;500;700&display=swap" rel="stylesheet">
<style>
  :root {
    --backdrop: #bdbdbd;
    --card: #ffffff;
    --navy: #22204f;
    --orange: #ee8a4c;
    --magenta: #c2187f;
    --ink: #2a2a2a;
  }
  * { margin: 0; padding: 0; box-sizing: border-box; }
  html, body { width: 1200px; height: 900px; overflow: hidden; }
  body {
    background: var(--backdrop);
    font-family: "Montserrat", sans-serif;
    position: relative;
  }
  .card {
    position: absolute;
    width: 540px;
    height: 310px;
    background: var(--card);
    border-radius: 26px;
    box-shadow: 0 6px 16px rgba(0,0,0,0.25);
    overflow: hidden;
  }
  .card--front { left: 50px; top: 110px; }
  .card--back { left: 610px; top: 480px; }

  .wordmark {
    display: flex;
    align-items: center;
    gap: 12px;
    color: var(--navy);
    font-weight: 500;
    letter-spacing: 0.04em;
    text-transform: uppercase;
  }
  .wordmark__dot {
    border-radius: 50%;
    background: var(--navy);
    flex: none;
  }
  .card--front .wordmark {
    position: absolute;
    left: 0; right: 0; top: 0; bottom: 0;
    justify-content: center;
    font-size: 38px;
  }
  .card--front .wordmark__dot { width: 30px; height: 30px; }

  .card--back .wordmark {
    position: absolute;
    left: 34px; top: 42px;
    font-size: 22px;
  }
  .card--back .wordmark__dot { width: 18px; height: 18px; }

  .credentials {
    position: absolute;
    right: 34px; top: 96px;
    text-align: right;
    font-size: 14px;
    line-height: 1.35;
    color: var(--ink);
  }
  .identity {
    position: absolute;
    left: 0; top: 150px;
    display: flex;
    align-items: stretch;
  }
  .identity__bar {
    width: 26px;
    background: var(--magenta);
    margin-top: 22px;
  }
  .identity__text { padding-left: 22px; }
  .identity__name {
    font-size: 27px;
    font-weight: 700;
    color: var(--orange);
    line-height: 1.1;
  }
  .identity__role {
    font-size: 17px;
    color: var(--ink);
  }
  .contact {
    position: absolute;
    left: 48px; top: 238px;
    list-style: none;
    font-size: 16px;
    color: var(--ink);
  }
  .contact__item {
    display: flex;
    align-items: center;
    gap: 10px;
    line-height: 1.55;
  }
  .contact__icon { width: 14px; height: 14px; flex: none; }
</style>
</head>
<body>
  <section class="card card--front" aria-label="Card front">
    <div class="wordmark">
      <span class="wordmark__dot"></span>
      <span>Skylark Reelworks</span>
    </div>
  </section>

  <section class="card card--back" aria-label="Card back">
    <div class="wordmark">
      <span class="wordmark__dot"></span>
      <span>Skylark Reelworks</span>
    </div>

    <p class="credentials">NRD Certified Remote Pilot<br>Fully Insured</p>

    <div class="identity">
      <span class="identity__bar"></span>
      <div class="identity__text">
        <p class="identity__name">Owen Tarrick</p>
        <p class="identity__role">Owner</p>
      </div>
    </div>

    <ul class="contact">
      <li class="contact__item">
        <svg class="contact__icon" viewBox="0 0 24 24" aria-hidden="true">
          <path fill="#ee8a4c" d="M6.6 10.8a15.1 15.1 0 0 0 6.6 6.6l2.2-2.2a1 1 0 0 1 1-.25 11.4 11.4 0 0 0 3.6.57 1 1 0 0 1 1 1V20a1 1 0 0 1-1 1A17 17 0 0 1 3 4a1 1 0 0 1 1-1h3.5a1 1 0 0 1 1 1c0 1.25.2 2.45.57 3.57a1 1 0 0 1-.25 1z"/>
        </svg>
        <span>614-502-7738</span>
      </li>
      <li class="contact__item">
        <svg class="contact__icon" viewBox="0 0 24 24" aria-hidden="true">
          <circle cx="12" cy="12" r="10" fill="none" stroke="#ee8a4c" stroke-width="2.4"/>
          <path d="M2 12h20M12 2c3 3 3 17 0 20M12 2c-3 3-3 17 0 20" fill="none" stroke="#ee8a4c" stroke-width="1.8"/>
        </svg>
        <span>www.skylarkreelworks.example</span>
      </li>
    </ul>
  </section>
</body>
</html>
```